Business Card Design of an established Waste Management, Plastic Recycling and Renewable Energy Comp

We are looking for business card design for plastic card with holograms (Very similar to credit card). I will provide our logo (Quenbys). So the name on the business card will be our logo )Quenbys) + Environmental next to it, so it will read Quenbys Environmental. The font for Environmental does not to be the same as the font of the logo. The holograms will be used to display ISO14001 Certified (In normal credit card, normally on the holograms, they show nova or kelo). I will post the design requirements from the card printing company very shortly to make sure they can use the design for the plastic card.

Target Market(s)

Companies, Government Organizations, Corporations.

Industry/Entity Type

Business

Contact Information for Business Card

Motto (Under the logo): Let's Get It Right
Name: Leopold Maresca; Position: Business Manager; Address: Pelmore Landfill & Recycling Facility, Tressingham Rd, Brindle Heights, WA 6140; Ph: +61 8 5210 4738; Mob: +61 455 903 172; E: Leo@quenbysenvironmental-mail.com

Requirements
Must have
• Business Names: Quenbys Logo + Environmental word after the logo.
• Motto (Under the logo): Let's Get It Right
• All the Business Card Details above.
• Hologram Logo on the lower right corner which says: ISO 14001 Certified.
• Please remember the design will be printed on plastic card Not paper. The plastic crad is the same as credit card. Hope this helps. Thank You

```html
<!DOCTYPE html>
<html lang="en">
<head>
<meta charset="utf-8">
<title>Quenbys Environmental – Business Card</title>
<link rel="stylesheet" href="https://fonts.googleapis.com/css2?family=Cinzel:wght@400&family=Open+Sans:wght@400;600&family=Varela+Round&display=swap">
<style>
  :root {
    --bg: #000000;
    --card: #ffffff;
    --ink: #1a1a1a;
    --grey-logo: #58585a;
    --blue-light: #1e9be0;
    --blue-mid: #1b7fc8;
    --blue-dark: #1d5a99;
  }
  * { margin: 0; padding: 0; box-sizing: border-box; }
  html, body { width: 1200px; height: 900px; overflow: hidden; background: var(--bg); }
  .canvas { position: relative; width: 1200px; height: 900px; }

  .card {
    position: absolute; top: 275px; width: 477px; height: 294px;
    background: var(--card); overflow: hidden;
    font-family: "Open Sans", Arial, sans-serif; color: var(--ink);
  }
  .card--front { left: 116px; border-radius: 0 52px 0 52px; }
  .card--back  { left: 622px; border-radius: 52px 0 52px 0; }

  .brand-mark {
    position: absolute; width: 56px; height: 56px; border-radius: 50%;
    background: linear-gradient(135deg, var(--blue-light), var(--blue-dark));
  }
  .brand-name {
    position: absolute; font-family: "Varela Round", Arial, sans-serif;
    color: var(--grey-logo); font-size: 44px; line-height: 1; letter-spacing: -0.5px;
  }
  .brand-sub {
    position: absolute; font-family: "Cinzel", Georgia, serif;
    color: var(--blue-mid); font-size: 14.5px; letter-spacing: 3.2px; line-height: 1;
  }

  /* front */
  .card--front .brand-mark { left: 28px; top: 34px; }
  .card--front .brand-name { left: 92px; top: 37px; }
  .card--front .brand-sub  { left: 95px; top: 86px; }

  .holder { position: absolute; right: 28px; top: 112px; text-align: right; }
  .holder__name { font-size: 17px; font-weight: 600; color: var(--blue-light); line-height: 1.1; }
  .holder__name span { color: var(--blue-dark); }
  .holder__role { font-size: 13px; line-height: 1.3; }

  .address { position: absolute; right: 26px; top: 164px; text-align: right; font-size: 13px; line-height: 17px; font-style: normal; }

  .contacts { position: absolute; right: 105px; top: 216px; list-style: none; font-size: 13px; line-height: 20px; }
  .contacts li { display: flex; justify-content: flex-end; align-items: center; gap: 8px; }
  .contacts svg { width: 10px; height: 10px; fill: var(--blue-light); }
  .divider { position: absolute; left: 377px; top: 218px; width: 1px; height: 56px; background: var(--blue-light); }
  .cert-badge {
    position: absolute; left: 387px; top: 218px; width: 64px; height: 52px;
    border: 1.5px solid var(--ink); border-radius: 6px;
  }
  .cert-badge::after {
    content: ""; position: absolute; left: 14px; top: 7px; width: 34px; height: 34px;
    border: 1px solid var(--ink); border-radius: 50%;
  }

  /* back */
  .accent-band {
    position: absolute; left: 0; top: 72px; width: 195px; height: 222px;
    background: linear-gradient(135deg, var(--blue-light) 0%, var(--blue-mid) 55%, var(--blue-dark) 100%);
  }
  .back-brand { position: absolute; left: 238px; top: 138px; width: 216px; text-align: center; }
  .back-brand .brand-name, .back-brand .brand-sub, .motto { position: static; display: block; }
  .back-brand .brand-sub { margin-top: 10px; }
  .motto { margin-top: 10px; font-size: 17px; font-weight: 600; color: var(--blue-light); }
  .motto span { color: var(--blue-dark); }
</style>
</head>
<body>
<div class="canvas">

  <section class="card card--front" aria-label="Business card front">
    <div class="brand-mark"></div>
    <div class="brand-name">Quenbys</div>
    <div class="brand-sub">ENVIRONMENTAL</div>

    <div class="holder">
      <p class="holder__name">Leopold <span>Maresca</span></p>
      <p class="holder__role">Business Manager</p>
    </div>

    <address class="address">
      Pelmore Landfill &amp; Recycling Facility<br>
      Tressingham Rd, Brindle Heights, WA 6140
    </address>

    <ul class="contacts">
      <li>+61 8 5210 4738
        <svg viewBox="0 0 10 10" aria-hidden="true"><path d="M2 0.5 L3.8 2.8 L2.9 4 Q4 6.2 6 7.1 L7.2 6.2 L9.5 8 L8.3 9.5 Q3.5 9 0.5 2 Z"/></svg></li>
      <li>+61 455 903 172
        <svg viewBox="0 0 10 10" aria-hidden="true"><rect x="2.5" y="0.5" width="5" height="9" rx="1"/></svg></li>
      <li>Leo@quenbysenvironmental-mail.com
        <svg viewBox="0 0 10 10" aria-hidden="true"><path d="M0.5 2 H9.5 V8.5 H0.5 Z M0.5 2 L5 5.5 L9.5 2" stroke="#fff" stroke-width="0.8"/></svg></li>
    </ul>
    <div class="divider"></div>
    <div class="cert-badge" role="img" aria-label="Certification hologram"></div>
  </section>

  <section class="card card--back" aria-label="Business card back">
    <div class="accent-band"></div>
    <div class="back-brand">
      <span class="brand-name">Quenbys</span>
      <span class="brand-sub">ENVIRONMENTAL</span>
      <span class="motto">Let's Get <span>It Right</span></span>
    </div>
  </section>

</div>
</body>
</html>
```